Business cards - BRENT Roofing & Siding

We need simple business cards made up for our Roofing & Siding business based in Calgary Alberta.
The logo on one side of the card and potentially our slogan "Built with trust, verified by time".
The other side could have:
-A small logo
-Rep name:
-Rep cell phone:
-Rep email:
-Office phone: 403-684-2093
-Website: PrairieShingleWorks.com

We would like to incorporate the colours from our logo, especially the lite blue on the jpeg file. I have attached the ai file and jpeg file. We like the colours better on the jpeg file.

I do not require a money back guarantee

```html
<!DOCTYPE html>
<html lang="en">
<head>
<meta charset="utf-8">
<title>BRENT Roofing &amp; Siding – Business Cards</title>
<link rel="stylesheet" href="https://fonts.googleapis.com/css2?family=Roboto:wght@400;500&amp;family=Exo+2:wght@500&amp;display=swap">
<style>
  :root {
    --page-bg: #2b2d31;
    --card-white: #ffffff;
    --brand-blue: #3d7cc9;
    --brand-blue-light: #4a8fd6;
    --ink-dark: #1c1c1c;
    --ink-grey: #444444;
    --accent-red: #e0312b;
  }
  * { margin: 0; padding: 0; box-sizing: border-box; }
  html, body {
    width: 1200px;
    height: 900px;
    overflow: hidden;
    background: var(--page-bg);
  }
  .sheet {
    width: 1200px;
    height: 900px;
    display: flex;
    flex-direction: column;
    align-items: center;
    justify-content: center;
    gap: 60px;
  }
  .card {
    width: 630px;
    height: 360px;
    position: relative;
    border-radius: 3px;
    box-shadow: 0 10px 30px rgba(0,0,0,0.35);
  }

  /* Front: rep details */
  .card-front { background: var(--card-white); }
  .card-front .edge-tab {
    position: absolute;
    left: 0;
    top: 44px;
    width: 10px;
    height: 30px;
    background: var(--brand-blue);
  }
  .rep {
    position: absolute;
    left: 40px;
    top: 40px;
    font-family: "Roboto", Arial, sans-serif;
  }
  .rep-name {
    font-size: 30px;
    font-weight: 500;
    color: var(--brand-blue);
    line-height: 1.1;
  }
  .rep-title {
    font-size: 15px;
    color: var(--ink-grey);
    margin-top: 4px;
  }
  .contact-list {
    list-style: none;
    margin-top: 18px;
  }
  .contact-list li {
    display: flex;
    align-items: center;
    gap: 8px;
    font-size: 14px;
    color: var(--ink-dark);
    line-height: 22px;
  }
  .contact-list svg { width: 12px; height: 12px; flex: none; }

  .wordmark {
    position: absolute;
    display: flex;
    align-items: center;
    gap: 12px;
    font-family: "Exo 2", "Roboto", sans-serif;
    font-weight: 500;
    letter-spacing: 0.12em;
    line-height: 1.05;
  }
  .wordmark-mark { width: 18px; height: 18px; flex: none; }
  .wordmark-name { display: block; }
  .wordmark-name .big { display: block; font-size: 44px; }
  .wordmark-name .small { display: block; font-size: 15px; }

  .card-front .wordmark { right: 40px; bottom: 44px; color: var(--ink-dark); }
  .card-front .wordmark-mark { background: var(--brand-blue); }

  /* Back: brand side */
  .card-back {
    background: linear-gradient(160deg, var(--brand-blue) 0%, var(--brand-blue-light) 100%);
  }
  .card-back .wordmark {
    left: 50%;
    top: 50%;
    transform: translate(-50%, -50%);
    color: var(--card-white);
  }
  .card-back .wordmark-mark { background: var(--card-white); }
</style>
</head>
<body>
<main class="sheet">
  <section class="card card-front" aria-label="Business card front">
    <span class="edge-tab"></span>
    <div class="rep">
      <p class="rep-name">Daniel Whitford</p>
      <p class="rep-title">President and CEO</p>
      <ul class="contact-list">
        <li>
          <svg viewBox="0 0 12 12" aria-hidden="true"><path d="M2.5 1l2 2.3-1 1.3a6 6 0 0 0 3.9 3.9l1.3-1L11 9.5 9.7 11C5 10.5 1.5 7 1 2.3z" fill="var(--accent-red)"/></svg>
          403-684-2093
        </li>
        <li>
          <svg viewBox="0 0 12 12" aria-hidden="true"><rect x="0.5" y="2" width="11" height="8" rx="1" fill="var(--accent-red)"/><path d="M1 2.5l5 4 5-4" stroke="#fff" stroke-width="1" fill="none"/></svg>
          info@prairieshingleworks.com
        </li>
        <li>
          <svg viewBox="0 0 12 12" aria-hidden="true"><circle cx="6" cy="6" r="5.2" fill="none" stroke="var(--accent-red)" stroke-width="1.3"/><path d="M1 6h10M6 1c-2.5 3-2.5 7 0 10M6 1c2.5 3 2.5 7 0 10" stroke="var(--accent-red)" stroke-width="1" fill="none"/></svg>
          prairieshingleworks.com
        </li>
      </ul>
    </div>
    <div class="wordmark">
      <span class="wordmark-mark"></span>
      <span class="wordmark-name"><span class="big">BRENT</span><span class="small">ROOFING &amp; SIDING</span></span>
    </div>
  </section>

  <section class="card card-back" aria-label="Business card back">
    <div class="wordmark">
      <span class="wordmark-mark"></span>
      <span class="wordmark-name"><span class="big">BRENT</span><span class="small">ROOFING &amp; SIDING</span></span>
    </div>
  </section>
</main>
</body>
</html>
```